wood grain ultrasonic essential oil aroma diffuser

Design a package that is simple but luxurious for the diffuser with my logo. My business is called “Open Petal Path”. The logo incorporates “Thoughts become things” the concept is positive thinking. I don’t particularly want the product featured as I have like to develop a uniform look for packaging and website and there are 2 different diffusers,

Target Market(s)

People interested in yoga, meditation, metaphysical aspects

Industry/Entity Type

Health And Wellness

Colors

Designer to choose colors to be used in the design.

Requirements
Must have
• Luxurious feel to packaging and alignment with the website

```html
<!DOCTYPE html>
<html lang="en">
<head>
<meta charset="utf-8">
<title>Open Petal Path – Ultrasonic Aroma Diffuser Packaging</title>
<link rel="stylesheet" href="https://fonts.googleapis.com/css2?family=Josefin+Sans:wght@300;400&display=swap">
<style>
  :root {
    --backdrop: #d8dcdf;
    --box-black: #0b0b0b;
    --side-black: #121212;
    --ink-light: #e6e6e6;
    --ink-muted: #bdbdbd;
    --gold-deep: #c8860e;
    --gold-bright: #f2cf4a;
    --gold-warm: #e39a1c;
    --pattern-rose: #e7a2b0;
    --pattern-mint: #9fd3c4;
    --pattern-lilac: #b7a4d8;
    --pattern-butter: #efdc98;
    --pattern-sky: #a7c3e6;
  }
  * { box-sizing: border-box; margin: 0; padding: 0; }
  html, body {
    width: 1200px; height: 1030px; overflow: hidden;
    background: var(--backdrop);
    font-family: "Josefin Sans", sans-serif;
  }
  .canvas {
    position: relative; width: 1200px; height: 1030px;
    display: flex; justify-content: center; align-items: center;
  }
  .dieline { display: flex; height: 720px; box-shadow: 0 18px 40px rgba(0,0,0,0.12); }

  /* Side panel */
  .side-panel {
    width: 210px; height: 100%;
    background: var(--side-black);
    color: var(--ink-light);
    padding: 56px 22px 0;
    display: flex; flex-direction: column; align-items: center;
    border-right: 1px solid #2a2a2a;
  }
  .side-title { text-align: center; line-height: 1.5; margin-bottom: 52px; }
  .side-title .subtitle { font-size: 13px; font-weight: 300; letter-spacing: 0.5px; }
  .side-title .product { font-size: 12px; font-weight: 400; letter-spacing: 1px; }
  .feature-list { list-style: none; width: 100%; display: flex; flex-direction: column; gap: 48px; }
  .feature { display: flex; align-items: center; gap: 12px; font-size: 11px; font-weight: 300; color: var(--ink-muted); }
  .feature svg { width: 22px; height: 30px; flex: none; stroke: var(--ink-light); fill: none; stroke-width: 1.4; }

  /* Front panel */
  .front-panel {
    position: relative; width: 470px; height: 100%;
    background: var(--box-black);
    color: var(--ink-light);
  }
  .pattern-strip {
    position: absolute; top: 0; bottom: 0; width: 30px;
  }
  .pattern-strip.left {
    left: 0;
    background: linear-gradient(180deg, var(--pattern-mint), var(--pattern-rose) 25%, var(--pattern-butter) 45%, var(--pattern-lilac) 62%, var(--pattern-sky) 80%, var(--pattern-rose));
  }
  .pattern-strip.right {
    right: 0;
    background: linear-gradient(180deg, var(--pattern-rose), var(--pattern-butter) 22%, var(--pattern-lilac) 42%, var(--pattern-rose) 60%, var(--pattern-sky) 78%, var(--pattern-mint));
  }
  .brand {
    position: absolute; top: 92px; left: 0; right: 0;
    display: flex; flex-direction: column; align-items: center; gap: 18px;
  }
  .brand-circle { width: 78px; height: 78px; border-radius: 50%; border: 2px solid var(--ink-light); }
  .brand-name { font-size: 22px; font-weight: 300; letter-spacing: 1.5px; color: var(--ink-light); }

  .title-frame {
    position: absolute; top: 360px; left: 50%; transform: translateX(-50%);
    width: 270px; height: 190px;
    border: 3px solid transparent;
    border-image: linear-gradient(135deg, var(--gold-bright), var(--gold-deep) 45%, var(--gold-warm) 70%, var(--gold-bright)) 1;
    display: flex; flex-direction: column; align-items: center; justify-content: center;
  }
  .title-line { font-size: 22px; font-weight: 300; letter-spacing: 1.5px; color: var(--ink-light); }
  .title-main { font-size: 34px; font-weight: 300; letter-spacing: 7px; margin-top: 10px; color: var(--ink-light); }

  .web-address {
    position: absolute; bottom: 44px; left: 0; right: 0;
    text-align: center; font-size: 11px; letter-spacing: 2.5px; color: var(--ink-light);
  }
</style>
</head>
<body>
<main class="canvas">
  <div class="dieline">
    <section class="side-panel">
      <div class="side-title">
        <p class="subtitle">Wood Grain Essential Oil</p>
        <p class="product">ULTRASONIC AROMA DIFFUSER</p>
      </div>
      <ul class="feature-list">
        <li class="feature"><svg viewBox="0 0 22 30"><circle cx="11" cy="10" r="6"/><line x1="11" y1="16" x2="11" y2="26"/></svg>Auto Off</li>
        <li class="feature"><svg viewBox="0 0 22 30"><rect x="5" y="3" width="12" height="24" rx="1"/><line x1="8" y1="10" x2="14" y2="10"/><line x1="8" y1="16" x2="14" y2="16"/></svg>Water Capacity 300ml</li>
        <li class="feature"><svg viewBox="0 0 22 30"><path d="M11 3a7 7 0 0 0-4 12.7V20h8v-4.3A7 7 0 0 0 11 3z"/><line x1="8" y1="24" x2="14" y2="24"/></svg>Colour Atmosphere Light</li>
        <li class="feature"><svg viewBox="0 0 22 30"><rect x="5" y="4" width="12" height="22" rx="2"/><polyline points="9,14 11,17 14,11"/></svg>Working Time 10hr</li>
        <li class="feature"><svg viewBox="0 0 22 30"><circle cx="11" cy="15" r="8"/><circle cx="11" cy="15" r="3"/></svg>Whisper Quiet Mist</li>
        <li class="feature"><svg viewBox="0 0 22 30"><path d="M6 11h4l5-5v18l-5-5H6z"/></svg>Low Noise 36dB</li>
      </ul>
    </section>

    <section class="front-panel">
      <div class="pattern-strip left" role="img" aria-label="Watercolour geometric pattern in pastel rose, mint, lilac and butter tones"></div>
      <div class="pattern-strip right" role="img" aria-label="Watercolour geometric pattern in pastel rose, mint, lilac and butter tones"></div>

      <div class="brand">
        <span class="brand-circle"></span>
        <p class="brand-name">Open Petal Path</p>
      </div>

      <div class="title-frame">
        <p class="title-line">Ultrasonic Aroma</p>
        <p class="title-main">DIFFUSER</p>
      </div>

      <p class="web-address">www.openpetalpath.org</p>
    </section>
  </div>
</main>
</body>
</html>
```